Upland Bird Hunting Preserve and Pointing Dog kennel

Need Price packages outlined for the bird hunting business. List the kennel and that we provide training and dogs for sale.
The preserve is "Tall Heron Provisions" the dog kennel is "Pine Hollow Setters"
1/2 Day Upland Field Hunts: 5 Pheasants $120
7 Chukar $125
Continental Hunt 12 Pheasants $325 includes meal, minimum 12 hunters
Guides available $100

Target Market(s)

upland bird hunters

Industry/Entity Type

hunting, outdoor

Colors
EE7325
F08F49
F5BC92
FAE3D3
FDF4ED

```html
<!DOCTYPE html>
<html lang="en">
<head>
<meta charset="utf-8">
<title>Tall Heron Provisions – Upland Hunts</title>
<link rel="stylesheet" href="https://fonts.googleapis.com/css2?family=Libre+Baskerville:ital,wght@0,400;0,700;1,400;1,700&display=swap">
<style>
  :root {
    --orange: #EE7325;
    --orange-mid: #F08F49;
    --peach: #F5BC92;
    --blush: #FAE3D3;
    --cream: #FDF4ED;
    --ink: #1c1c1c;
    --white: #ffffff;
  }
  * { margin: 0; padding: 0; box-sizing: border-box; }
  html, body { width: 927px; height: 1200px; overflow: hidden; }
  body {
    font-family: "Libre Baskerville", Georgia, serif;
    color: var(--ink);
    background: var(--white);
  }
  .flyer { position: relative; width: 927px; height: 1200px; background: var(--white); }
  .band-left { position: absolute; left: 0; top: 0; width: 113px; height: 1200px; background: var(--orange); }
  .band-right { position: absolute; right: 0; top: 0; width: 114px; height: 1200px; background: var(--blush); }
  .center { position: absolute; left: 113px; width: 700px; text-align: center; }

  .brand { top: 32px; font-size: 30px; font-weight: 700; color: var(--orange); letter-spacing: .5px; }
  .town { top: 70px; font-size: 23px; font-weight: 700; }
  .tagline { top: 104px; font-size: 20px; letter-spacing: 2.5px; }

  .photo { position: absolute; }
  .photo-hunters { left: 124px; top: 145px; width: 678px; height: 257px;
    background: linear-gradient(180deg, #b9b2a6 0%, #8e826f 45%, #6b5c48 75%, #a69a86 100%); }

  .offer-title { font-size: 24px; font-weight: 700; }
  .offer-line { font-size: 20px; line-height: 28px; }
  .offer-line.italic { font-style: italic; }
  .divider { position: absolute; left: 300px; width: 326px; height: 1px; background: var(--peach); }

  .kennel-card { position: absolute; left: 149px; top: 758px; width: 270px; height: 173px;
    background: var(--blush); border-radius: 18px; display: flex; flex-direction: column;
    align-items: center; justify-content: center; gap: 10px; padding-right: 34px; }
  .kennel-name, .kennel-town { font-size: 17px; font-weight: 700; color: var(--ink); }
  .kennel-mark { width: 16px; height: 16px; border-radius: 50%; background: var(--ink); }

  .kennel-frame { position: absolute; left: 387px; top: 722px; width: 426px; height: 247px;
    background: var(--blush); border-radius: 18px 0 0 18px; padding: 9px 0 9px 9px; }
  .photo-kennel { width: 100%; height: 100%; border-radius: 12px 0 0 12px;
    background: linear-gradient(180deg, #b6ab9a 0%, #8a7d6a 50%, #5d5145 100%); }

  .services { position: absolute; left: 113px; top: 996px; width: 470px; text-align: center;
    font-size: 21px; font-style: italic; line-height: 34px; }
  .services strong { font-weight: 700; }

  .contact { position: absolute; left: 158px; top: 1090px; width: 396px; height: 54px;
    border: 2px solid var(--orange-mid); border-radius: 27px; background: var(--white);
    display: flex; align-items: center; justify-content: center; font-size: 20px; }
  .contact-label { position: absolute; top: -12px; left: 50%; transform: translateX(-50%);
    background: var(--white); padding: 0 10px; font-size: 15px; letter-spacing: 2px;
    color: var(--orange-mid); font-weight: 700; }
  .contact strong { font-weight: 700; }

  .dog-frame { position: absolute; left: 600px; top: 991px; width: 175px; height: 160px;
    background: var(--ink); border-radius: 10px; padding: 6px; }
  .photo-dog { width: 100%; height: 100%; border-radius: 6px;
    background: linear-gradient(160deg, #c9a86a 0%, #a88550 55%, #5a4a35 100%); }
</style>
</head>
<body>
<main class="flyer">
  <div class="band-left"></div>
  <div class="band-right"></div>

  <header>
    <h1 class="center brand">TALL HERON PROVISIONS, LLC</h1>
    <p class="center town">Alder Creek, MO</p>
    <p class="center tagline">LICENSED SHOOTING PRESERVE</p>
  </header>

  <div class="photo photo-hunters" role="img" aria-label="Group of hunters standing behind a log lined with harvested pheasants in a winter woodland"></div>

  <section class="center" style="top:422px">
    <h2 class="offer-title">½ DAY UPLAND FIELD HUNTS</h2>
    <p class="offer-line">5 Pheasants — $120</p>
    <p class="offer-line">7 Chukar — $125</p>
  </section>
  <div class="divider" style="top:524px"></div>

  <section class="center" style="top:532px">
    <h2 class="offer-title">CONTINENTAL PHEASANT HUNT</h2>
    <p class="offer-line italic">12 Pheasants — $325 (includes meal)</p>
    <p class="offer-line italic">12 Hunter Minimum</p>
  </section>
  <div class="divider" style="top:626px"></div>

  <section class="center" style="top:642px">
    <h2 class="offer-title">GUIDES AVAILABLE</h2>
    <p class="offer-line italic">$100 per half day</p>
  </section>

  <div class="kennel-frame">
    <div class="photo-kennel" role="img" aria-label="Hunters in blaze orange with a white pointing dog and the day's birds on a truck tailgate"></div>
  </div>
  <div class="kennel-card">
    <span class="kennel-mark"></span>
    <span class="kennel-name">PINE HOLLOW SETTERS</span>
    <span class="kennel-town">BIRCH FORD, MO</span>
  </div>

  <p class="services">Professional <strong>dog training</strong> available<br>Puppies and started dogs <strong>for sale!</strong></p>

  <div class="contact">
    <span class="contact-label">CONTACT</span>
    <span><strong>DALE WHITMORE</strong> : 555-014-2276</span>
  </div>

  <div class="dog-frame">
    <div class="photo-dog" role="img" aria-label="Pointing dog standing in tall golden grass"></div>
  </div>
</main>
</body>
</html>
```